Lawn care business card

I am looking for a quality designed personal business card to represent the quality and elegant nature of our company. We separate ourselves in our market by the aesthetic value of our work, so I am looking for marketing material that does the same. We target our marketing high end customers, and we try to avoid price shoppers. I am open to all design options, so long as they are in line with our companies values.

We are tend to go with a retro look on everything from our logo and print material, to our uniforms. We like to portray and "old fashion" set of core values, with a modern elegance. So a wild and crazy look is out of the question.

Things I'd like on the card:
1.) Logo
2.) Phone number: (816) 555-2931
3.) Website: Verdelynkc.com
4.) Email: robertfairley@verdelynkc.com
5.) My name: Robert Fairley
6.) Facebook link: friendwall.com/VerdelynGardenandGrounds
7.) Instagram: http://photoloop.com/verdelynkc

Attached is a copy of our logo.

Reason: More time is needed to gather conclusive feedback from the members of our marketing team.

```html
<!DOCTYPE html>
<html lang="en">
<head>
<meta charset="utf-8">
<title>Verdelyn – Business Card</title>
<link href="https://fonts.googleapis.com/css2?family=Open+Sans:wght@600;700&display=swap" rel="stylesheet">
<style>
  :root {
    --bg: #e9e6e1;
    --card: #ffffff;
    --orange: #f05a22;
    --ink: #1d1d1d;
    --light: #ffffff;
  }
  * { margin: 0; padding: 0; box-sizing: border-box; }
  html, body { width: 1200px; height: 800px; overflow: hidden; background: var(--bg); }
  .canvas { position: relative; width: 1200px; height: 800px; display: flex; align-items: center; justify-content: center; }
  .card {
    position: relative; width: 1050px; height: 600px; background: var(--card);
    box-shadow: 0 10px 30px rgba(0,0,0,.18); overflow: hidden;
    font-family: "Open Sans", Arial, sans-serif;
  }
  .card-band { position: absolute; inset: 0; width: 100%; height: 100%; }
  .brand { position: absolute; left: 150px; top: 110px; display: flex; align-items: center; gap: 18px; }
  .brand-dot { width: 64px; height: 64px; border-radius: 50%; background: var(--orange); }
  .brand-name { font-size: 54px; font-weight: 700; color: var(--ink); letter-spacing: 3px; text-transform: uppercase; }
  .holder-name {
    position: absolute; right: 60px; top: 200px; font-size: 34px; font-weight: 700;
    color: var(--ink); letter-spacing: 2.5px;
  }
  .contact-list { position: absolute; right: 40px; top: 420px; list-style: none; }
  .contact-item {
    display: flex; justify-content: flex-end; align-items: center; gap: 12px;
    color: var(--light); font-size: 21px; font-weight: 600; letter-spacing: 1px; height: 31px;
  }
  .contact-icon { width: 20px; height: 20px; flex: none; }
</style>
</head>
<body>
<div class="canvas">
  <div class="card">
    <svg class="card-band" viewBox="0 0 1050 600" preserveAspectRatio="none" aria-hidden="true">
      <path fill="none" stroke="#1d1d1d" stroke-width="8" d="M0 300 Q525 380 1050 340"/>
      <path fill="#f05a22" d="M0 330 Q525 410 1050 370 L1050 600 L0 600 Z"/>
    </svg>

    <div class="brand">
      <span class="brand-dot"></span>
      <span class="brand-name">Verdelyn</span>
    </div>

    <p class="holder-name">Robert Fairley</p>

    <ul class="contact-list">
      <li class="contact-item">(816) 555-2931
        <svg class="contact-icon" viewBox="0 0 20 20"><path fill="#fff" d="M5 2l3 4-2 2c1 2 3 4 5 5l2-2 4 3-2 3C8 17 3 12 2 5z"/></svg>
      </li>
      <li class="contact-item">Verdelynkc.com
        <svg class="contact-icon" viewBox="0 0 20 20"><circle cx="10" cy="10" r="8" fill="none" stroke="#fff" stroke-width="2"/><path d="M2 10h16M10 2c-4 4-4 12 0 16M10 2c4 4 4 12 0 16" fill="none" stroke="#fff" stroke-width="1.5"/></svg>
      </li>
      <li class="contact-item">robertfairley@verdelynkc.com
        <svg class="contact-icon" viewBox="0 0 20 20"><rect x="1" y="4" width="18" height="12" fill="#fff"/><path d="M1 4l9 7 9-7" fill="none" stroke="#f05a22" stroke-width="1.5"/></svg>
      </li>
      <li class="contact-item">http://photoloop.com/verdelynkc
        <svg class="contact-icon" viewBox="0 0 20 20"><rect x="1" y="1" width="18" height="18" rx="3" fill="#fff"/></svg>
      </li>
      <li class="contact-item">friendwall.com/VerdelynGardenandGrounds
        <svg class="contact-icon" viewBox="0 0 20 20"><rect x="1" y="1" width="18" height="18" rx="3" fill="#fff"/></svg>
      </li>
    </ul>
  </div>
</div>
</body>
</html>
```